U.S. Popcorn company needs business cards

We are a popcorn company that manufactures popcorn and sells it to grocery stores worldwide. Our theme is "Americana" and our logo is U.S. route 66 which is the most famous highway in the U.S.

We would like the design to be simple and to use both sides. On the back side we would like to see just the logo and website. The front would be normal details

Target Market(s)

Wholesalers, grocers and distributors

Industry/Entity Type

Manufacture

Contact Information for Business Card

Business name: Prairie Lantern Popcorn
Phone: +1 555 308 4726
Email: Dale@prairielanternpopcorn.com
website: www.prairielanternpopcorn.com
Tag Line: "POPping with flavor"
Name: Dale Whitcombe
Title: Founder/President

Requirements
Must have
• Either this design should be fun or clean and simple. I will let you show me your thougths.
Nice to have
• Anything that ties in the real Hwy Route 66.
• Colors might need to be red, white and blue incorporated.
Should not have
• Not be too busy.

```html
<!DOCTYPE html>
<html lang="en">
<head>
<meta charset="utf-8">
<title>Prairie Lantern Popcorn – Business Cards</title>
<link href="https://fonts.googleapis.com/css2?family=Open+Sans:ital,wght@0,400;0,600;0,700;0,800;1,400&display=swap" rel="stylesheet">
<style>
  :root {
    --backdrop: #e4e4e4;
    --card: #f7f7f7;
    --navy: #1c2d66;
    --red: #c8201f;
    --ink: #26336a;
    --rule: #d4d4d8;
  }
  * { box-sizing: border-box; margin: 0; padding: 0; }
  html, body {
    width: 1200px; height: 576px; overflow: hidden;
    background: var(--backdrop);
    font-family: "Open Sans", Arial, sans-serif;
  }
  .canvas { position: relative; width: 1200px; height: 576px; }
  .card {
    position: absolute; top: 138px; height: 294px;
    background: var(--card); border-radius: 6px; overflow: hidden;
  }
  .card--back { left: 80px; width: 486px; }
  .card--front { left: 602px; width: 480px; }

  /* back side */
  .brand-mark {
    position: absolute; left: 0; right: 0; top: 99px;
    text-align: center; color: var(--navy);
    font-weight: 800; font-size: 34px; line-height: 1.12;
    text-transform: uppercase; letter-spacing: 0.5px;
  }
  .back-web {
    position: absolute; left: 0; right: 0; top: 256px;
    display: flex; align-items: center; justify-content: center; gap: 12px;
    font-size: 11.5px; font-weight: 700; color: var(--navy);
  }
  .back-web .rule { width: 52px; height: 2px; background: var(--navy); border-radius: 1px; }
  .accent { color: var(--red); }

  /* front side */
  .front-brand {
    position: absolute; left: 24px; top: 105px; width: 172px;
    text-align: center; color: var(--navy);
    font-weight: 800; font-size: 20px; line-height: 1.15; text-transform: uppercase;
  }
  .divider { position: absolute; left: 210px; top: 60px; width: 1px; height: 146px; background: var(--rule); }
  .person { position: absolute; left: 238px; top: 70px; }
  .person__name { color: var(--red); font-weight: 600; font-size: 16px; line-height: 1.2; }
  .person__title { color: var(--ink); font-style: italic; font-size: 11.5px; margin-top: 1px; }
  .contacts { position: absolute; left: 238px; top: 146px; list-style: none; }
  .contacts li {
    display: flex; align-items: center; gap: 12px;
    font-size: 12.5px; color: var(--ink); height: 17.5px;
  }
  .contacts svg { width: 11px; height: 11px; fill: var(--red); flex: none; }
  .band-red { position: absolute; left: 0; bottom: 4px; width: 210px; height: 19px; background: var(--red); }
  .band-navy {
    position: absolute; right: 0; bottom: 4px; width: 296px; height: 36px;
    background: var(--navy); clip-path: polygon(24px 0, 100% 0, 100% 100%, 0 100%);
  }
  .tagline {
    position: absolute; left: 238px; bottom: 12px;
    color: #fff; font-size: 13.5px; letter-spacing: 0.2px;
  }
  .tagline b { font-weight: 700; }
</style>
</head>
<body>
<main class="canvas">
  <section class="card card--back" aria-label="Card back">
    <div class="brand-mark">Prairie Lantern<br>Popcorn</div>
    <div class="back-web">
      <span class="rule"></span>
      <span>www.<span class="accent">prairielanternpopcorn</span>.com</span>
      <span class="rule"></span>
    </div>
  </section>

  <section class="card card--front" aria-label="Card front">
    <div class="front-brand">Prairie<br>Lantern<br>Popcorn</div>
    <div class="divider"></div>
    <div class="person">
      <p class="person__name">Dale Whitcombe</p>
      <p class="person__title">Founder/President</p>
    </div>
    <ul class="contacts">
      <li>
        <svg viewBox="0 0 12 12" aria-hidden="true"><path d="M1 3.2C1 2 2.2 1 6 1s5 1 5 2.2V4.4H8.4V3.4H3.6v1H1z M2.4 5.2h7.2l1 5.8H1.4z M6 6.6a1.6 1.6 0 1 0 0 3.2 1.6 1.6 0 0 0 0-3.2z"/></svg>
        <span>+1 555 308 4726</span>
      </li>
      <li>
        <svg viewBox="0 0 12 12" aria-hidden="true"><path d="M0.5 2.5h11v7h-11z" /><path d="M0.8 2.8 6 7l5.2-4.2" fill="none" stroke="#f7f7f7" stroke-width="1"/></svg>
        <span>Dale@prairielanternpopcorn.com</span>
      </li>
      <li>
        <svg viewBox="0 0 12 12" aria-hidden="true"><circle cx="6" cy="6" r="5.2"/><path d="M0.8 6h10.4M6 0.8v10.4M2 3.4h8M2 8.6h8" stroke="#f7f7f7" stroke-width="0.7" fill="none"/><ellipse cx="6" cy="6" rx="2.3" ry="5.2" fill="none" stroke="#f7f7f7" stroke-width="0.7"/></svg>
        <span>www.<span class="accent">prairielanternpopcorn</span>.com</span>
      </li>
    </ul>
    <div class="band-red"></div>
    <div class="band-navy"></div>
    <p class="tagline">"<b>POP</b>ping with flavor"</p>
  </section>
</main>
</body>
</html>
```